Bluefern Business Services needs a new interactive and interesting website

We need an interesting, professional, modern and functional company website for Bluefern Business Services - a young IT Services company based out of Chennai, India.

Bluefern Business Services is a fully owned subsidiary of Marlow Goods, one of the world's leading direct to consumer wine merchant.

We already have a registered company logo which must feature in the website.

We conceive, design, develop, test, implement and support IT solutions across the entire Marlow Goods IT landscape. For ex : We currently run about 25 e-commerce websites for Marlow Goods on ATG and Dot Net.

We would like to see our corporate colors used in the website. (Burgundy wine and wine green - source: www.bluefernbs-site.com)

We are looking at this website to communicate a fun, friendly and professionally managed company - reaching out to career seekers, prospective customers and general public.

For reference - The company name 'Bluefern' is an inspiration from the Marlow Goods lineage.

The second image with the world map is stickered on our main entrance to the office, I am not sure where this can be used -just putting it out there..

Please note that there are only a few more days to submit designs for this contest  !

I would appreciate if you can help posting your designs in time for our review and consideration.

Thanks.

Reason: Thanks for your inputs. We have a number of designers and a lot to digest and work with in the past few days. There has been a rush of new designs in the last few days Hence we will require more time to process these and make our decision. Hence i am requesting the contest to be open for more days. Regards, Tarun

Target Market(s)

Prospective job seekers who want to know more about the company and also wish to apply for a job vacancy
People wanting to know more about the company in general and our progress
People who want to see what we offer and how we can help them too - prospective customers
Companies that are interested in our IT Captive journey and are looking for a business opportunity

Industry/Entity Type

E-Commerce

Requirements
Must have
• Log In/ Register facility acting as a Single Sign on for Intranet (Employees)

Facility to post job vacancies (with an expiry date) and enable people to apply for a role and upload their CV/Resume.

Facility to Review Job applications

Facility for website visitors to contact Bluefern business Services via an online 'Contact Us' form with a split of job seekers and business opportunities

Gallery facility to upload pictures regarding company events
Nice to have
• Less Cluttered and contemporary design
Some Wine/Vineyard inspirations will be good but not too much, the company is an IT services company

```html
<!DOCTYPE html>
<html lang="en">
<head>
<meta charset="utf-8">
<title>Bluefern Business Services</title>
<link rel="stylesheet" href="https://fonts.googleapis.com/css2?family=Open+Sans:wdth,wght@75..100,300..700&family=Varela+Round&display=swap">
<style>
:root{
  --burgundy:#8e0b45;
  --burgundy-dark:#5d0328;
  --burgundy-text:#7a1038;
  --olive:#7b8a2c;
  --text:#444;
  --muted:#8a8a8a;
  --line:#d8d8d8;
  --nav-bg:#e9e9e9;
  --footer-bg:#e6e6e6;
}
*{box-sizing:border-box;margin:0;padding:0}
html,body{width:1045px;height:1200px;overflow:hidden}
body{position:relative;background:#fff;font-family:"Open Sans",sans-serif;color:var(--text)}
.abs{position:absolute}
.header-band{left:0;top:0;width:1045px;height:403px;background:linear-gradient(180deg,#a10c55 0%,#8e0b45 60%,#7a0838 100%)}
.vine-photo{right:0;top:0;width:500px;height:403px;
  background:
    radial-gradient(ellipse 140px 90px at 78% 10%,rgba(120,135,175,.85),rgba(60,65,95,0) 70%),
    radial-gradient(ellipse 120px 80px at 52% 8%,rgba(95,120,70,.7),rgba(95,120,70,0) 70%),
    radial-gradient(ellipse 90px 140px at 95% 60%,rgba(120,60,60,.8),rgba(120,60,60,0) 70%),
    radial-gradient(ellipse 260px 260px at 75% 25%,rgba(45,40,60,.9),rgba(122,8,56,0) 75%)}
.logo{left:86px;top:22px;display:flex;align-items:flex-start;gap:8px;color:#fff}
.logo-dot{width:30px;height:30px;border-radius:50%;background:#fff;margin-top:10px}
.logo-name{font-family:"Varela Round",sans-serif;font-size:40px;line-height:44px}
.logo-sub{font-size:21px;line-height:24px;margin-left:2px}
.appointment{right:82px;top:49px;text-align:right;color:#fff}
.appointment .label{font-size:13px;font-weight:600}
.appointment .phone{font-size:21px;font-weight:600;line-height:26px}
.main-nav{left:81px;top:103px;width:882px;height:43px;display:flex;background:var(--nav-bg)}
.main-nav a{flex:1;display:flex;align-items:center;justify-content:center;text-decoration:none;color:#666;font-size:14px;font-weight:500;border-right:1px solid #cfcfcf;background:linear-gradient(#f4f4f4,#e2e2e2)}
.main-nav a:last-child{border-right:none}
.main-nav a.active{background:linear-gradient(#8e0b45,#5d0328);color:#fff}
.hero{left:81px;top:146px;width:882px;height:326px;overflow:hidden;border:1px solid #ddd}
.hero-photo{position:absolute;inset:0;
  background:
    radial-gradient(ellipse 90px 120px at 6% 40%,rgba(90,60,45,.8),rgba(90,60,45,0) 70%),
    radial-gradient(ellipse 120px 140px at 10% 90%,rgba(60,80,120,.8),rgba(60,80,120,0) 70%),
    radial-gradient(ellipse 90px 110px at 26% 35%,rgba(215,170,140,.8),rgba(215,170,140,0) 70%),
    radial-gradient(ellipse 130px 160px at 30% 80%,rgba(240,240,240,.9),rgba(240,240,240,0) 70%),
    radial-gradient(ellipse 110px 150px at 48% 50%,rgba(120,125,130,.8),rgba(120,125,130,0) 70%),
    radial-gradient(ellipse 90px 110px at 60% 30%,rgba(220,180,150,.9),rgba(220,180,150,0) 70%),
    radial-gradient(ellipse 120px 170px at 62% 85%,rgba(95,95,100,.9),rgba(95,95,100,0) 70%),
    linear-gradient(180deg,#d9dadb 0%,#c3c4c4 55%,#8b8d92 100%)}
.hero-panel{position:absolute;inset:0}
.hero-title{position:absolute;left:614px;top:84px;color:#fff;font-size:31px;line-height:31px;font-weight:400;letter-spacing:.3px}
.hero-text{position:absolute;left:616px;top:152px;width:250px;color:#f1f3df;font-size:11.5px;line-height:19.5px;font-weight:300}
.hero-arrows{position:absolute;left:840px;top:294px}
h2.section-title{font-size:22.5px;font-weight:400;color:#333;letter-spacing:-.2px}
.welcome{left:84px;top:507px;width:310px}
.welcome .tagline{color:var(--olive);font-size:14.5px;font-weight:500;margin:8px 0 6px 3px}
.welcome p{font-size:10.8px;line-height:19px;margin:0 0 8px 3px}
.opps{left:408px;top:509px;width:270px}
.opp{margin-left:2px}
.opp:first-of-type{margin-top:12px}
.opp .date{color:var(--burgundy-text);font-size:12.5px}
.opp .role{font-size:11.2px;margin-top:4px}
.opp .desc{font-size:9.5px;line-height:17px;color:var(--muted);font-weight:300;margin-top:2px}
.opp + .opp{margin-top:11px}
.services{left:698px;top:502px;width:266px;height:212px;border:1px solid #d5d5d5;border-radius:3px;overflow:hidden}
.services h3{height:43px;background:linear-gradient(#8e0b45,#5d0328);color:#fff;font-size:19.5px;font-weight:400;padding:8px 0 0 22px}
.services ul{list-style:none;padding:8px 28px 0 16px}
.services li{font-size:11.2px;color:#333;height:27.6px;line-height:27px;border-bottom:1px solid var(--line);padding-left:12px;position:relative;white-space:nowrap}
.services li::before{content:"";position:absolute;left:1px;top:11px;border-left:5px solid #999;border-top:3px solid transparent;border-bottom:3px solid transparent}
.divider{left:81px;top:743px;width:883px;height:1px;background:#ddd}
.events-title{left:84px;top:767px}
.event{width:300px;height:110px}
.event-thumb{position:absolute;left:0;top:0;width:130px;height:102px}
.event-thumb .play{position:absolute;left:47px;top:33px}
.event-body{position:absolute;left:139px;top:-3px;width:142px}
.event-body h4{color:var(--burgundy-text);font-size:13px;font-weight:400}
.event-body p{font-size:11px;line-height:18px;color:var(--muted);margin-top:2px}
.footer{left:0;top:1106px;width:1045px;height:94px;background:var(--footer-bg);border-top:1px solid #d2d2d2}
.footer-nav{position:absolute;left:88px;top:25px;font-size:13px;font-stretch:85%;color:#333;font-weight:500}
.footer-nav span{margin:0 5px}
.copyright{position:absolute;left:88px;top:55px;font-size:10px;color:#888}
.social{position:absolute;left:867px;top:20px;display:flex;gap:4px}
.social span{width:25px;height:25px;border-radius:50%;background:#555;color:#fff;font-size:9px;font-weight:600;display:flex;align-items:center;justify-content:center}
</style>
</head>
<body>
<div class="abs header-band"></div>
<div class="abs vine-photo" role="img" aria-label="Photo of dark grapes hanging on a vine"></div>

<div class="abs logo">
  <span class="logo-dot"></span>
  <div>
    <div class="logo-name">bluefern</div>
    <div class="logo-sub">Business Services</div>
  </div>
</div>

<div class="abs appointment">
  <div class="label">Make an Appointment</div>
  <div class="phone">+91 (44) 40012345</div>
</div>

<nav class="abs main-nav">
  <a class="active" href="#">HOME</a>
  <a href="#">ABOUT US</a>
  <a href="#">CLIENTS</a>
  <a href="#">SERVICES</a>
  <a href="#">CAREERS</a>
  <a href="#">CONTACT US</a>
</nav>

<section class="abs hero">
  <div class="hero-photo" role="img" aria-label="Photo of a smiling business team seated around a meeting table"></div>
  <svg class="hero-panel" width="882" height="326" viewBox="0 0 882 326">
    <defs>
      <linearGradient id="panelGrad" x1="0" y1="0" x2="1" y2="1">
        <stop offset="0" stop-color="#8f9c3a"/>
        <stop offset="1" stop-color="#6e7e22"/>
      </linearGradient>
    </defs>
    <path d="M610 0 C520 80 560 260 650 326 L882 326 L882 0 Z" fill="#fff" opacity=".85"/>
    <path d="M622 0 C540 80 575 255 665 326 L882 326 L882 0 Z" fill="url(#panelGrad)"/>
  </svg>
  <h1 class="hero-title">Provide Software<br>Consulting</h1>
  <p class="hero-text">Suspendisse vulputate aliquam dui. Nulla elementum dui ut augue. Aliquam vehicula mi at mauris Maecenas placerat nisl</p>
  <svg class="hero-arrows" width="30" height="20" viewBox="0 0 30 20">
    <path d="M10 2 L3 10 L10 18 M20 2 L27 10 L20 18" fill="none" stroke="#fff" stroke-width="1.8"/>
  </svg>
</section>

<section class="abs welcome">
  <h2 class="section-title">Welcome to Our Website!</h2>
  <div class="tagline">Delivering IT Excellence</div>
  <p>Welcome to Bluefern Business Services, an emerging provider of global IT consulting and software services.</p>
  <p>We are part of the Marlow Goods group, a family run business and the world's largest multi-channel home delivery wine merchant. Ut accumsan ultricies elit. Maecenas at justo id velit placerat molestie. Donec dictum lectus non odio. Cras a ante vitae enim iaculis aliquam.</p>
</section>

<section class="abs opps">
  <h2 class="section-title" style="font-weight:300">Latest Opportunities</h2>
  <div class="opp">
    <div class="date">26/11/2013</div>
    <div class="role">Software Developers/Programmer Analysts - AX</div>
    <div class="desc">Class aptent taciti sociosqu ad litora torquent per conubia nostra, per inceptos hymenaeos.</div>
  </div>
  <div class="opp">
    <div class="date">28/11/2013</div>
    <div class="role">Aliquam nec erat at purus cursus</div>
    <div class="desc">Proin nulla arcu, nonummy luctus, dictum eget, fermentum et, lorem. Nunc porta convallis pede.</div>
  </div>
</section>

<aside class="abs services">
  <h3>Services We Provide</h3>
  <ul>
    <li>Packaged Applications</li>
    <li>Enterprise Application Integration</li>
    <li>Digital Commerce</li>
    <li>Application Development &amp; Maintenance</li>
    <li>Business Software Consulting</li>
  </ul>
</aside>

<div class="abs divider"></div>
<h2 class="abs section-title events-title">Our Latest Events</h2>

<div class="abs event" style="left:83px;top:812px">
  <div class="event-thumb" role="img" aria-label="Event photo of guests raising glasses at a party" style="background:radial-gradient(ellipse 40px 50px at 50% 25%,rgba(240,220,190,.7),rgba(240,220,190,0) 70%),linear-gradient(135deg,#8a7560,#2b2628 70%,#3a4560)">
    <svg class="play" width="36" height="36" viewBox="0 0 36 36"><circle cx="18" cy="18" r="17" fill="#fff" opacity=".8"/><path d="M14 10 L26 18 L14 26 Z" fill="#222"/></svg>
  </div>
  <div class="event-body"><h4>Event Tittle/Date</h4><p>Mauris nunc quam, venenatis nec, euismod sit amet, egestas placerat, est. Pellentesque habitant morbi tristique</p></div>
</div>
<div class="abs event" style="left:385px;top:812px">
  <div class="event-thumb" role="img" aria-label="Event photo of a conference audience" style="background:radial-gradient(ellipse 60px 40px at 40% 20%,rgba(230,235,240,.8),rgba(230,235,240,0) 70%),linear-gradient(160deg,#b8c0c6,#5a6168 60%,#2f3338)">
    <svg class="play" width="36" height="36" viewBox="0 0 36 36"><circle cx="18" cy="18" r="17" fill="#fff" opacity=".8"/><path d="M14 10 L26 18 L14 26 Z" fill="#222"/></svg>
  </div>
  <div class="event-body"><h4>Event Tittle/Date</h4><p>Mauris nunc quam, venenatis nec, euismod sit amet, egestas placerat, est. Pellentesque habitant morbi tristique</p></div>
</div>
<div class="abs event" style="left:690px;top:812px">
  <div class="event-thumb" role="img" aria-label="Event photo of a banquet table set for dinner" style="background:radial-gradient(ellipse 30px 60px at 40% 60%,rgba(245,245,240,.9),rgba(245,245,240,0) 70%),linear-gradient(135deg,#d2ad6c,#6a5a50 55%,#2a3458)">
    <svg class="play" width="36" height="36" viewBox="0 0 36 36"><circle cx="18" cy="18" r="17" fill="#fff" opacity=".8"/><path d="M14 10 L26 18 L14 26 Z" fill="#222"/></svg>
  </div>
  <div class="event-body"><h4>Event Tittle/Date</h4><p>Mauris nunc quam, venenatis nec, euismod sit amet, egestas placerat, est. Pellentesque habitant morbi tristique</p></div>
</div>
<div class="abs event" style="left:81px;top:946px">
  <div class="event-thumb" role="img" aria-label="Event photo of colleagues talking in an office" style="background:radial-gradient(ellipse 40px 50px at 25% 60%,rgba(220,225,235,.8),rgba(220,225,235,0) 70%),linear-gradient(135deg,#c4855a,#6e4a38 55%,#2e2a2a)">
    <svg class="play" width="36" height="36" viewBox="0 0 36 36"><circle cx="18" cy="18" r="17" fill="#fff" opacity=".8"/><path d="M14 10 L26 18 L14 26 Z" fill="#222"/></svg>
  </div>
  <div class="event-body"><h4>Event Tittle/Date</h4><p>Mauris nunc quam, venenatis nec, euismod sit amet, egestas placerat, est. Pellentesque habitant morbi tristique</p></div>
</div>
<div class="abs event" style="left:383px;top:946px">
  <div class="event-thumb" role="img" aria-label="Event photo of a panel discussion in front of an audience" style="background:linear-gradient(180deg,#7a3a30 0%,#a5685a 45%,#e6e3dc 70%,#cfcac0 100%)">
    <svg class="play" width="36" height="36" viewBox="0 0 36 36"><circle cx="18" cy="18" r="17" fill="#fff" opacity=".8"/><path d="M14 10 L26 18 L14 26 Z" fill="#222"/></svg>
  </div>
  <div class="event-body"><h4>Event Tittle/Date</h4><p>Mauris nunc quam, venenatis nec, euismod sit amet, egestas placerat, est. Pellentesque habitant morbi tristique</p></div>
</div>
<div class="abs event" style="left:688px;top:946px">
  <div class="event-thumb" role="img" aria-label="Event photo of a crowd mingling at a reception" style="background:radial-gradient(ellipse 40px 40px at 50% 35%,rgba(210,220,235,.8),rgba(210,220,235,0) 70%),linear-gradient(135deg,#9a6650,#5a3c40 50%,#3c4660)">
    <svg class="play" width="36" height="36" viewBox="0 0 36 36"><circle cx="18" cy="18" r="17" fill="#fff" opacity=".8"/><path d="M14 10 L26 18 L14 26 Z" fill="#222"/></svg>
  </div>
  <div class="event-body"><h4>Event Tittle/Date</h4><p>Mauris nunc quam, venenatis nec, euismod sit amet, egestas placerat, est. Pellentesque habitant morbi tristique</p></div>
</div>

<footer class="abs footer">
  <div class="footer-nav">HOME<span>|</span>ABOUT US<span>|</span>CLIENTS<span>|</span>SERVICES<span>|</span>CAREERS<span>|</span>CONTACT US</div>
  <div class="copyright">Copyright © 2013 Company Name.&nbsp; All right reserved</div>
  <div class="social" aria-label="Social media links"><span>Vu</span><span>Zo</span><span>Qi</span></div>
</footer>
</body>
</html>
```